lofty birch website

We need a new website for our new business division. We are a sustainable design firm specializing in servicing the needs if architects and developers. We have a staff consisting of architects, engineers, and former contractors and we understand green must make sense.

Bottomline - the only sustainable and lofty birch solutions are those thatbare good for the environment and good for our clients bottom line.

Our company is lofty birch and we will send you a copy of our logo you will see our tagline. Is simple. sustainable. solutions. The play with the periods is that we believe their are simple sustainable solutions and we want to use the words together and possible let each stand alone to accentuate their individual meaning in regards to benefit to our clients.

We want a cool splash page with nich graphics and pictures then later pages to feature projects and design ideas.

Target Market(s)

Our target customers are architects, developers, and contractors who would need assistance with the design process for a VARO project or assisatnce with a building owner who wants to make tehir facilty more environmentally friendly and save energy costs at the same tiem.

Industry/Entity Type

Environment

Requirements
Must have
• Needs a construction look with an environmentally friendly surrounding that is pleasing to look at. Must appeal to the client not only as environmentally friendly but also a wise investment.
Nice to have
• Opportunity for a connection to Social networking including a blog.
Should not have
• A totally environmental building feel at whatever cost. We want to emphasize that it is possible to build environmental friendly and save you money over the life of your building

```html
<!DOCTYPE html>
<html lang="en">
<head>
<meta charset="utf-8">
<title>lofty birch — simple. sustainable. solutions.</title>
<link rel="stylesheet" href="https://fonts.googleapis.com/css2?family=Michroma&family=Poiret+One&family=Josefin+Sans:wght@600&family=Open+Sans:wght@400&display=swap">
<style>
  :root {
    --white: #ffffff;
    --leaf: #5cc021;
    --lime: #b5e02a;
    --aqua: #38d3dc;
    --teal-deep: #0b4a3e;
    --teal: #137a66;
    --rule-green: #4fb32a;
    --accent-red: #e00000;
    --ink: #1d1d1d;
    --logo-grey: #5b5b5b;
    --photo-light: #d9d9d9;
    --photo-dark: #3a3a3a;
  }
  * { box-sizing: border-box; margin: 0; padding: 0; }
  html, body { width: 1200px; height: 900px; overflow: hidden; background: var(--white); }

  .page {
    position: relative;
    width: 1200px;
    height: 900px;
    overflow: hidden;
    background:
      linear-gradient(to bottom, rgba(255,255,255,0) 0, rgba(255,255,255,0) 740px, rgba(255,255,255,0.95) 830px, #fff 900px),
      linear-gradient(to bottom, #fff 0, #fff 110px, rgba(255,255,255,0) 260px),
      radial-gradient(ellipse 260px 360px at 1130px 450px, var(--teal-deep) 0, rgba(11,74,62,0.6) 50%, rgba(11,74,62,0) 100%),
      radial-gradient(ellipse 240px 330px at 920px 470px, var(--teal) 0, rgba(19,122,102,0) 100%),
      radial-gradient(ellipse 300px 160px at 620px 610px, var(--aqua) 0, rgba(56,211,220,0) 100%),
      radial-gradient(ellipse 360px 260px at 80px 500px, var(--lime) 0, rgba(181,224,42,0.6) 40%, rgba(181,224,42,0) 100%),
      radial-gradient(ellipse 560px 230px at 400px 530px, var(--leaf) 0, rgba(92,192,33,0.5) 55%, rgba(92,192,33,0) 100%),
      linear-gradient(to bottom, #f4fbf5 0, #d7f2e4 300px, #9fe0b7 520px, #c9eef0 700px, #fff 900px);
  }

  .top-rule {
    position: absolute; left: 0; top: 112px; width: 1200px; height: 2px;
    background: linear-gradient(to right, rgba(79,179,42,0), var(--rule-green) 30%, var(--rule-green) 70%, rgba(79,179,42,0));
  }

  .tagline-banner {
    position: absolute; top: 143px; left: 0; width: 1200px; height: 40px;
    font-family: "Michroma", sans-serif; font-size: 24px; font-weight: 400; color: var(--white);
    text-shadow: 0 2px 4px rgba(0,0,0,0.35);
    letter-spacing: 3px;
  }
  .tagline-banner span { position: absolute; top: 0; }
  .tagline-banner .w1 { left: 287px; }
  .tagline-banner .w2 { left: 457px; }
  .tagline-banner .w3 { left: 722px; }

  .feature-photo {
    position: absolute; left: 115px; top: 301px; width: 337px; height: 228px;
    border: 4px solid var(--white); border-radius: 3px;
    box-shadow: 0 0 8px 2px rgba(120,230,90,0.9);
    background: linear-gradient(135deg, var(--photo-dark) 0, #9a9a9a 35%, var(--photo-light) 55%, #6d6d6d 100%);
  }

  .red-tab { position: absolute; background: var(--accent-red); }
  .red-tab.description-tab { left: 502px; top: 305px; width: 18px; height: 6px; }
  .red-tab.thumb-tab { left: 79px; top: 757px; width: 24px; height: 8px; }

  .project-description {
    position: absolute; left: 502px; top: 317px; width: 149px; height: 191px;
    background: linear-gradient(to bottom, #5fe0c4 0, #47d79a 55%, #37cc6e 100%);
    box-shadow: 0 0 6px rgba(0,0,0,0.15);
    padding: 32px 10px 0 14px;
    font-family: "Josefin Sans", sans-serif; font-size: 8.5px; line-height: 12.5px;
    text-transform: uppercase; color: var(--ink);
  }

  .main-nav {
    position: absolute; right: 43px; top: 320px; text-align: right;
    font-family: "Poiret One", sans-serif; font-size: 25px; line-height: 34px;
    text-transform: uppercase; color: var(--ink); list-style: none;
  }
  .main-nav a { color: inherit; text-decoration: none; }
  .nav-marker {
    position: absolute; left: 1159px; top: 326px; width: 4px; height: 86px;
    background: linear-gradient(to bottom, #7ff2e0, #2fc9c0);
  }

  .thumb-strip {
    position: absolute; left: 0; top: 648px; width: 1200px; height: 104px;
    background: linear-gradient(to right, rgba(255,255,255,0.35), rgba(255,255,255,0.2) 60%, rgba(255,255,255,0));
  }
  .thumb {
    position: absolute; top: 648px; height: 104px;
    box-shadow: 0 2px 8px rgba(0,0,0,0.45);
  }
  .thumb.stairwell { left: 79px; width: 153px; background: linear-gradient(135deg, #2d2d2d, #bdbdbd 50%, #5a5a5a); }
  .thumb.glass-office { left: 248px; width: 157px; background: linear-gradient(160deg, #f2f2f2 0, #bfbfbf 45%, #575757 100%); }
  .thumb.log-cabin { left: 423px; width: 158px; background: linear-gradient(to bottom, #cfcfcf 0, #7a7a7a 45%, #4a4a4a 70%, #b4b4b4 100%); }
  .thumb.tower { left: 601px; width: 78px; background: linear-gradient(100deg, #3e3e3e, #c7c7c7 55%, #6a6a6a); }

  .social-links { position: absolute; left: 40px; top: 823px; display: flex; gap: 19px; }
  .social-links a {
    width: 48px; height: 48px; display: flex; align-items: center; justify-content: center;
    border-radius: 3px; text-decoration: none;
    font-family: "Open Sans", sans-serif; font-size: 10px; color: var(--white);
  }
  .social-links .murmur { background: #4fb8e3; }
  .social-links .kinly { background: #3b5a98; }

  .brand {
    position: absolute; left: 912px; top: 812px; width: 250px;
    font-family: "Open Sans", sans-serif; color: var(--logo-grey);
  }
  .brand-name { font-size: 34px; line-height: 38px; letter-spacing: -0.5px; }
  .brand-tagline { font-size: 14px; line-height: 16px; padding-left: 6px; letter-spacing: 0.3px; }
</style>
</head>
<body>
<main class="page">
  <div class="top-rule"></div>

  <h1 class="tagline-banner">
    <span class="w1">simple</span>
    <span class="w2">sustainable</span>
    <span class="w3">solutions</span>
  </h1>

  <div class="feature-photo" role="img" aria-label="Black and white photo looking up a modern stairwell toward a skylight"></div>

  <div class="red-tab description-tab"></div>
  <section class="project-description">
    <p>Discription of your project will be displayed here.</p>
  </section>

  <ul class="main-nav">
    <li><a href="#home">Home</a></li>
    <li><a href="#projects">Projects</a></li>
    <li><a href="#contacts">Contacts</a></li>
  </ul>
  <div class="nav-marker"></div>

  <div class="thumb-strip"></div>
  <div class="thumb stairwell" role="img" aria-label="Thumbnail: stairwell under skylight"></div>
  <div class="thumb glass-office" role="img" aria-label="Thumbnail: curved glass office building"></div>
  <div class="thumb log-cabin" role="img" aria-label="Thumbnail: wooden cabin among trees"></div>
  <div class="thumb tower" role="img" aria-label="Thumbnail: high-rise towers seen from below"></div>
  <div class="red-tab thumb-tab"></div>

  <nav class="social-links" aria-label="Social networks">
    <a class="murmur" href="#murmur">Murmur</a>
    <a class="kinly" href="#kinly">Kinly</a>
  </nav>

  <div class="brand">
    <div class="brand-name">lofty birch</div>
    <div class="brand-tagline">simple. sustainable. solutions.</div>
  </div>
</main>
</body>
</html>
```